Brightmill Data Works

Our company is about IT hardwares and IT solutions. IT hardware such as PC, RAMS, storage and servers. IT solutions such as project management, BA. We are also selling new technology too.

Target Market(s)

Consumer, Small to Medium Business, Corporate

Requirements
Must have
• The business card must have the following:
• Name:
• Title:
• Contact Number:
• Email address:
• Website:
• Color: Must match the logo color upgrade

```html
<!DOCTYPE html>
<html lang="en">
<head>
<meta charset="utf-8">
<title>Brightmill Data Works – Business Card</title>
<link rel="stylesheet" href="https://fonts.googleapis.com/css2?family=Montserrat:wght@600;700;800&family=Arimo:wght@400;700&display=swap">
<style>
  :root {
    --bg: #2b2b2b;
    --card-dark: #2e2e2e;
    --card-white: #f6f6f6;
    --gold: #d4922f;
    --text-light: #f2f2f2;
    --text-dark: #333333;
  }
  * { margin: 0; padding: 0; box-sizing: border-box; }
  html, body { width: 1200px; height: 997px; overflow: hidden; }
  body { background: var(--bg); position: relative; font-family: "Arimo", Arial, sans-serif; }

  .card {
    position: absolute;
    width: 540px;
    height: 310px;
    border-radius: 18px;
    overflow: hidden;
    box-shadow: 0 14px 30px rgba(0,0,0,0.45);
  }
  .card-front { left: 100px; top: 130px; background: var(--card-dark); }
  .card-back { left: 560px; top: 500px; background: var(--card-white); }

  .wordmark {
    position: absolute;
    display: flex;
    align-items: center;
    gap: 14px;
    font-family: "Montserrat", Arial, sans-serif;
    font-weight: 800;
    text-transform: uppercase;
    letter-spacing: 1px;
    line-height: 1.1;
    white-space: nowrap;
  }
  .wordmark-dot { width: 18px; height: 18px; border-radius: 50%; background: var(--gold); flex: none; }
  .wordmark-text { display: flex; flex-direction: column; }
  .card-front .wordmark { left: 50%; top: 50%; transform: translate(-50%, -50%); font-size: 34px; color: var(--text-light); }
  .card-back .wordmark { right: 34px; top: 92px; font-size: 25px; color: var(--text-dark); }

  .card-shapes { position: absolute; inset: 0; }

  .contact-block { position: absolute; left: 34px; top: 112px; color: var(--text-light); }
  .person-name {
    font-family: "Montserrat", Arial, sans-serif;
    font-weight: 700; font-size: 19px; color: var(--gold); letter-spacing: 0.5px;
  }
  .person-title { font-size: 16px; margin-top: 4px; }
  .contact-list { list-style: none; margin-top: 22px; }
  .contact-list li { display: flex; align-items: center; gap: 10px; font-size: 17px; line-height: 24px; }
  .contact-icon { width: 15px; height: 15px; flex: none; }
  .website { font-weight: 700; color: var(--gold); letter-spacing: 1px; margin-top: 2px; font-size: 18px; }
</style>
</head>
<body>

<section class="card card-front">
  <div class="wordmark"><span class="wordmark-dot"></span><span class="wordmark-text"><span>Brightmill</span><span>Data Works</span></span></div>
</section>

<section class="card card-back">
  <svg class="card-shapes" viewBox="0 0 540 310" preserveAspectRatio="none" aria-hidden="true">
    <path d="M160 0 L215 0 Q268 130 272 310 L262 310 Q250 130 160 0 Z" fill="var(--gold)"/>
    <path d="M0 0 L160 0 Q250 130 262 310 L0 310 Z" fill="var(--card-dark)"/>
  </svg>

  <div class="wordmark"><span class="wordmark-dot"></span><span class="wordmark-text"><span>Brightmill</span><span>Data Works</span></span></div>

  <div class="contact-block">
    <div class="person-name">OWEN HARLOW</div>
    <div class="person-title">Director</div>
    <ul class="contact-list">
      <li>
        <svg class="contact-icon" viewBox="0 0 16 16"><circle cx="8" cy="8" r="8" fill="var(--gold)"/><path d="M5 4.5l1.5-.5 1 2-1 .8a5 5 0 0 0 2.7 2.7l.8-1 2 1-.5 1.5c-3.5 0-6.5-3-6.5-6.5z" fill="#fff"/></svg>
        206.555.0142
      </li>
      <li>
        <svg class="contact-icon" viewBox="0 0 16 16"><circle cx="8" cy="8" r="8" fill="var(--gold)"/><rect x="5.5" y="3.5" width="5" height="9" rx="1" fill="#fff"/></svg>
        425.555.0197
      </li>
      <li>
        <svg class="contact-icon" viewBox="0 0 16 16"><circle cx="8" cy="8" r="8" fill="var(--gold)"/><rect x="4" y="5" width="8" height="6" fill="#fff"/><path d="M4 5l4 3 4-3" stroke="var(--gold)" fill="none"/></svg>
        owen@bmdw.com
      </li>
      <li class="website">www.bmdw.com</li>
    </ul>
  </div>
</section>

</body>
</html>
```